Business Cards for IT Consulting Company (Managed Service Provider)

I am looking to have some business cards printed and would like some designs. We are an IT Consulting company based in Vancouver BC. I would like a nice clean and modern look to the cards. I have uploaded all the versions of my logo so parts can be used as needed. Here is a snippit from our website homepage:

Quillbrook Networks Ltd. is an IT Solutions Partner located in Vancouver BC, Canada. We offer IT solutions and support to customers in the greater Vancouver Area. With expertise in Microsoft platforms, as well as Linux and Mac OSX and over 12 years experience in the IT industry, Quillbrook Networks is dedicated to offering our clients top quality service and products. We take pride in the solutions we offer our customers. The greatest compliment a client can give us is to recommend our services.

Quillbrook Networks Ltd. offers a wide range of IT services from onsite service to remote support and managed service solutions. This allows clients to choose the support path that best suits their company’s needs. Supporting many different sized companies from small to enterprise level over the past 12 years Quillbrook Networks has the experience and expertise needed to ensure things run smoothly. Allowing our clients to focus on doing business.

Revolutionizing the way IT services are delivered.

Quillbrook Networks is dedicated to providing our clients with IT solutions that work and grow with them for years to come. This philosophy helps save money in the long run instead of replacing equipment constantly. Far too often IT solutions are not well thought out and while possibly solving the problem at hand, require replacement due to growth or quality within a very short time frame. Quillbrook Networks takes pride in providing solutions that will last and be able to accommodate growth without the need for replacement.

Industry/Entity Type

Information Technology

Contact Information for Business Card

Quillbrook Networks Ltd.
(Employee Name)
Eml: (Employees Email Address)
Web: quillbrook.me
Ph: 604-555-0148

Font styles to use
Serif
Sans Serif

Requirements
Must have
• The Company logo and company colors.
Nice to have
• - Our tag line: "Revolutionizing IT Services" or "Revolutionizing the way IT services are delivered."
• - Also I really like the idea of nature and technology together blending which is sort of where my logo came from so integrating that somehow onto the business cards would be great.

```html
<!DOCTYPE html>
<html lang="en">
<head>
<meta charset="utf-8">
<title>Quillbrook Networks Ltd. – Business Card</title>
<link rel="stylesheet" href="https://fonts.googleapis.com/css2?family=Montserrat:wght@400;600;700&display=swap">
<style>
  :root {
    --backdrop: #2b2b2d;
    --card-white: #ffffff;
    --card-grey: #5e5f61;
    --brand-blue: #1aa3e8;
    --text-white: #ffffff;
    --marker-white: #f2f2f2;
  }
  * { margin: 0; padding: 0; box-sizing: border-box; }
  html, body {
    width: 1200px; height: 900px; overflow: hidden;
    background: var(--backdrop);
    font-family: "Montserrat", Arial, sans-serif;
  }
  .canvas { position: relative; width: 1200px; height: 900px; }

  .card {
    position: absolute;
    width: 640px; height: 366px;
    overflow: hidden;
    box-shadow: 0 14px 30px rgba(0,0,0,.45);
  }

  /* Front */
  .card-front { left: 110px; top: 60px; background: var(--card-white); }
  .tagline {
    position: absolute; left: 0; right: 0; top: 166px;
    text-align: center;
    color: var(--brand-blue);
    font-weight: 600; font-size: 24px; letter-spacing: .5px;
  }
  .front-web {
    position: absolute; right: 40px; bottom: 40px;
    color: var(--brand-blue); font-weight: 700; font-size: 14px; letter-spacing: .5px;
  }

  /* Back */
  .card-back { left: 450px; top: 474px; background: var(--card-grey); }
  .corner-panel { position: absolute; right: 0; top: 0; }
  .brand {
    position: absolute; left: 44px; top: 96px;
    display: flex; align-items: center; gap: 14px;
  }
  .brand-square { width: 22px; height: 22px; background: var(--brand-blue); }
  .brand-name {
    color: var(--brand-blue); font-weight: 700; font-size: 30px; letter-spacing: .3px;
  }
  .contact-block { position: absolute; left: 0; top: 206px; }
  .side-marker { position: absolute; left: 0; top: 36px; display: flex; }
  .side-marker span { width: 12px; height: 14px; }
  .side-marker .m-white { background: var(--marker-white); }
  .side-marker .m-blue { background: var(--brand-blue); }
  .person { margin-left: 60px; }
  .person-name {
    color: var(--brand-blue); font-weight: 700; font-size: 22px; letter-spacing: 2.5px;
  }
  .person-role {
    color: var(--text-white); font-weight: 600; font-size: 14px; letter-spacing: 1px; margin-top: 2px;
  }
  .contact-list { list-style: none; margin-top: 12px; }
  .contact-list li {
    display: flex; align-items: center; gap: 12px;
    color: var(--text-white); font-weight: 600; font-size: 14px; letter-spacing: .8px;
    line-height: 24px;
  }
  .contact-list svg { width: 12px; height: 12px; flex: none; }
</style>
</head>
<body>
<main class="canvas">

  <section class="card card-front" aria-label="Card front">
    <p class="tagline">Revolutionizing IT Services</p>
    <p class="front-web">www.quillbrook.me</p>
  </section>

  <section class="card card-back" aria-label="Card back">
    <svg class="corner-panel" width="640" height="366" viewBox="0 0 640 366" aria-hidden="true">
      <polygon points="430,0 640,0 640,250" fill="#ffffff"/>
    </svg>

    <div class="brand">
      <span class="brand-square"></span>
      <span class="brand-name">Quillbrook Networks Ltd.</span>
    </div>

    <div class="contact-block">
      <div class="side-marker"><span class="m-white"></span><span class="m-blue"></span></div>
      <div class="person">
        <p class="person-name">MARLO KEATING</p>
        <p class="person-role">DIRECTOR</p>
        <ul class="contact-list">
          <li>
            <svg viewBox="0 0 12 12"><path d="M2.5 1 L4.5 1 L5 3.5 L3.8 4.4 C4.5 6 6 7.5 7.6 8.2 L8.5 7 L11 7.5 L11 9.5 C11 10.3 10.3 11 9.5 11 C5 11 1 7 1 2.5 C1 1.7 1.7 1 2.5 1 Z" fill="#1aa3e8"/></svg>
            604-555-0148
          </li>
          <li>
            <svg viewBox="0 0 12 12"><rect x="1" y="2.5" width="10" height="7" fill="none" stroke="#1aa3e8" stroke-width="1.3"/><polyline points="1,3 6,6.8 11,3" fill="none" stroke="#1aa3e8" stroke-width="1.3"/></svg>
            info@marlokeating.com
          </li>
          <li>
            <svg viewBox="0 0 12 12"><circle cx="6" cy="6" r="5" fill="none" stroke="#1aa3e8" stroke-width="1.2"/><ellipse cx="6" cy="6" rx="2.2" ry="5" fill="none" stroke="#1aa3e8" stroke-width="1"/><line x1="1" y1="6" x2="11" y2="6" stroke="#1aa3e8" stroke-width="1"/></svg>
            www.quillbrook.me
          </li>
        </ul>
      </div>
    </div>
  </section>

</main>
</body>
</html>
```